Website for Briar Hollow Gathering Church

Wordpress website design required for Briar Hollow Gathering Church. We are a family oriented church catering for age groups from school age to elderly people. The church has a wide variety of activities which it coordinates. The idea is to describe the activities on the activities page, but cross-link them to show which would be applicable to the different age groups.

We would like an inviting website which is easy to read and navigate.

Target Market(s)

Very wide audience - from school age youth to elderly people, so design and style should cater for both audiences.

Industry/Entity Type

Church

Coding

Coded - Design and coding required

Number of Pages Required

5+ page

Font styles to use
Sans Serif

Colors
0255a3
ffffff
0792cd
f78f20

Requirements
Must have
• Inviting website.
• Clear readable font.
• Space to import photos to balance text on each page.
• Need to project a dynamic and progressive feel for the church.
• Easy to navigate.
Nice to have
• Scrolling photos on pages. Ability to enter questions/ comments/prayer requests on Home page.
Should not have
• Conservative audience, so should not be too bold.

```html
<!DOCTYPE html>
<html lang="en">
<head>
<meta charset="utf-8">
<title>Briar Hollow Gathering Church</title>
<link href="https://fonts.googleapis.com/css2?family=Raleway:wght@400;500;600;700&family=Open+Sans:wght@400;600;700&display=swap" rel="stylesheet">
<style>
:root{
  --blue:#0255a3;
  --blue-dark:#0a3d8f;
  --sky:#0792cd;
  --orange:#f47b20;
  --white:#ffffff;
  --ink:#333333;
  --muted:#555555;
  --line:#dddddd;
  --soft:#f2f2f2;
  --footer:#2b2b2b;
  --footer-base:#222222;
}
*{box-sizing:border-box;margin:0;padding:0}
html,body{width:1200px;height:2528px;overflow:hidden}
body{position:relative;background:var(--white);font-family:"Open Sans",Arial,sans-serif;color:var(--ink)}
.heading{font-family:"Raleway",Arial,sans-serif;font-weight:400}
.abs{position:absolute}

/* header */
.site-header{position:absolute;left:0;top:0;width:1200px;height:105px;background:var(--white)}
.brand{position:absolute;left:135px;top:56px;display:flex;align-items:center;gap:8px}
.brand-dot{width:10px;height:10px;border-radius:50%;background:var(--blue)}
.brand-name{font-family:"Open Sans",Arial,sans-serif;font-weight:600;font-size:15px;color:var(--blue)}
.search{position:absolute;left:1050px;top:22px}
.main-nav a{position:absolute;top:72px;font-size:12px;color:#222;text-decoration:none;letter-spacing:.2px}
.main-nav a.active{color:var(--blue)}
.nav-underline{position:absolute;left:548px;top:101px;width:42px;height:3px;background:var(--blue)}

/* hero */
.hero{position:absolute;left:0;top:105px;width:1200px;height:480px;background:linear-gradient(100deg,#2a2522 0%,#4a3b33 40%,#6a5548 60%,#3a3230 100%)}
.hero-shade{position:absolute;inset:0;background:linear-gradient(90deg,rgba(0,0,0,.45),rgba(0,0,0,.1))}
.hero-kicker{position:absolute;left:131px;top:142px;font-family:"Raleway",Arial,sans-serif;font-weight:600;font-size:20px;color:var(--white)}
.hero-title{position:absolute;left:129px;top:175px;font-family:"Raleway",Arial,sans-serif;font-weight:600;font-size:47px;color:var(--white);letter-spacing:.5px}
.hero-btn{position:absolute;left:131px;top:240px;width:141px;height:38px;background:var(--blue);color:var(--white);font-size:11px;font-weight:700;display:flex;align-items:center;justify-content:center;border-radius:2px}
.hero-dots{position:absolute;left:133px;top:316px;display:flex;gap:7px}
.hero-dots span{width:8px;height:8px;border-radius:50%;background:#bbb}
.hero-dots span.on{background:var(--blue)}

/* welcome */
.welcome-title{position:absolute;left:0;width:1200px;top:616px;text-align:center;font-size:34px;color:var(--blue)}
.welcome-text{position:absolute;left:200px;width:800px;top:680px;text-align:center;font-size:11.5px;line-height:20px;color:var(--ink)}
.feature{position:absolute;top:769px;width:280px;text-align:center}
.feature-icon{width:106px;height:106px;border-radius:50%;border:1.5px solid var(--blue);margin:0 auto;display:flex;align-items:center;justify-content:center}
.feature-icon.solid{background:var(--blue)}
.feature-title{margin-top:26px;font-size:20px;color:#222;letter-spacing:.3px}
.feature-text{margin-top:20px;font-size:11.5px;line-height:19.5px;color:var(--ink)}

/* mission */
.mission{position:absolute;left:0;top:1078px;width:1200px;height:262px;background:var(--orange)}
.mission-title{position:absolute;left:0;width:1200px;top:36px;text-align:center;font-size:32px;color:var(--white)}
.mission-text{position:absolute;left:220px;width:760px;top:96px;text-align:center;font-size:11.5px;line-height:19.5px;color:var(--white)}
.mission-btn{position:absolute;left:539px;top:181px;width:111px;height:42px;border:1px solid var(--white);color:var(--white);font-size:12px;display:flex;align-items:center;justify-content:center}

/* photos */
.photos-title{position:absolute;left:0;width:1200px;top:1394px;text-align:center;font-size:31px;color:#222}
.photo{position:absolute;top:1473px;width:225px;height:185px}
.arrow{position:absolute;top:1548px}

/* news */
.news{position:absolute;left:0;top:1709px;width:1200px;height:507px;background:var(--soft)}
.news-title{position:absolute;left:0;width:1200px;top:45px;text-align:center;font-size:31px;color:#222}
.card{position:absolute;top:111px;width:286px;height:364px;background:var(--white);border:1px solid var(--line)}
.card-image{position:absolute;left:0;top:0;width:284px;height:185px}
.card-date{position:absolute;left:0;top:118px;width:64px;height:67px;background:var(--blue);color:var(--white);text-align:center;font-family:"Raleway",Arial,sans-serif}
.card-date .day{display:block;font-size:23px;margin-top:7px}
.card-date .mon{display:block;font-size:15px;margin-top:2px}
.card-title{position:absolute;left:20px;top:210px;font-size:20px;color:var(--blue)}
.card-text{position:absolute;left:20px;width:246px;top:242px;font-size:11.5px;line-height:19px;color:var(--ink);text-align:justify}

/* footer */
.site-footer{position:absolute;left:0;top:2216px;width:1200px;height:237px;background:var(--footer);color:#ddd}
.footer-brand{position:absolute;left:131px;top:108px;display:flex;align-items:center;gap:8px}
.footer-brand .brand-dot{background:var(--white);width:12px;height:12px}
.footer-brand .brand-name{color:var(--white);font-size:17px}
.footer-col{position:absolute;top:42px}
.footer-head{font-family:"Raleway",Arial,sans-serif;font-size:15px;color:var(--white);letter-spacing:.3px}
.quick-links{list-style:none;margin-top:18px}
.quick-links li{font-size:10.5px;line-height:20px;color:#ddd}
.contact-line{display:flex;gap:14px;font-size:10.5px;line-height:20px;color:#ddd;margin-top:16px}
.contact-line.tight{margin-top:8px}
.contact-line svg{flex:none;margin-top:5px}
.socials{display:flex;gap:7px;margin-top:16px}
.socials span{width:37px;height:37px;border-radius:50%;background:#8a8a8a}
.socials span.on{background:var(--orange)}
.footer-base{position:absolute;left:0;top:2453px;width:1200px;height:75px;background:var(--footer-base);text-align:center;font-size:10.5px;line-height:75px;color:#ccc}
</style>
</head>
<body>

<header class="site-header">
  <div class="brand"><span class="brand-dot"></span><span class="brand-name">Briar Hollow Gathering Church</span></div>
  <svg class="search" width="16" height="16" viewBox="0 0 16 16"><circle cx="6.5" cy="6.5" r="5" fill="none" stroke="#111" stroke-width="2.2"/><line x1="10.2" y1="10.2" x2="14.5" y2="14.5" stroke="#111" stroke-width="2.6" stroke-linecap="round"/></svg>
  <nav class="main-nav">
    <a class="active" style="left:553px" href="#">HOME</a>
    <a style="left:625px" href="#">AGE GROUP</a>
    <a style="left:730px" href="#">ACTIVITES</a>
    <a style="left:822px" href="#">EVENTS</a>
    <a style="left:901px" href="#">ABOUT BHGC</a>
    <a style="left:1016px" href="#">CONTACT</a>
  </nav>
  <div class="nav-underline"></div>
</header>

<section class="hero" role="img" aria-label="Church members sharing a meal at long tables in the church hall">
  <div class="hero-shade"></div>
  <div class="hero-kicker">WE ARE A FAMILY ORIENTED</div>
  <div class="hero-title">CHURCH CATERING</div>
  <div class="hero-btn">VIEW DETAILS</div>
  <div class="hero-dots"><span class="on"></span><span></span><span></span></div>
</section>

<h1 class="welcome-title heading">WELCOME TO BHGC</h1>
<p class="welcome-text">Our Catholic faith is beautiful, dynamic, and engaging. Your website should be, too. Our responsive designs will inspire and engage your visitors on all devices. Choose a design from our growing collection of beautiful Catholic themes or let our team create a completely custom design just for you.</p>

<div class="feature" style="left:104px">
  <div class="feature-icon solid">
    <svg width="34" height="36" viewBox="0 0 34 36" fill="none" stroke="#fff" stroke-width="1.6"><path d="M17 4c-6 0-9 4.5-9 10v8l-3 5h24l-3-5v-8c0-5.5-3-10-9-10z"/><path d="M13 30a4 4 0 0 0 8 0"/><line x1="17" y1="1" x2="17" y2="4"/></svg>
  </div>
  <h2 class="feature-title heading">PRAYER REQUEST</h2>
  <p class="feature-text">Neque porro quisquam est, qui dolorem ipsum quia dolor sit amet, consectetur, adipisci velit, sed quia non numquam eius modi tempora</p>
</div>
<div class="feature" style="left:460px">
  <div class="feature-icon">
    <svg width="34" height="34" viewBox="0 0 34 34" fill="none" stroke="#0255a3" stroke-width="1.6"><rect x="6" y="4" width="22" height="26" rx="2"/><line x1="6" y1="25" x2="28" y2="25"/><path d="M13 4v12l3-2 3 2V4"/></svg>
  </div>
  <h2 class="feature-title heading">SERVICE TIMES</h2>
  <p class="feature-text">Neque porro quisquam est, qui dolorem ipsum quia dolor sit amet, consectetur, adipisci velit, sed quia non numquam eius modi tempora</p>
</div>
<div class="feature" style="left:797px">
  <div class="feature-icon">
    <svg width="36" height="34" viewBox="0 0 36 34" fill="none" stroke="#0255a3" stroke-width="1.6" stroke-linejoin="round"><path d="M18 3l4.3 9.5 10.2 1-7.7 6.8 2.3 10.2L18 25.3 8.9 30.5l2.3-10.2L3.5 13.5l10.2-1z"/></svg>
  </div>
  <h2 class="feature-title heading">MESSAGE</h2>
  <p class="feature-text">Neque porro quisquam est, qui dolorem ipsum quia dolor sit amet, consectetur, adipisci velit, sed quia non numquam eius modi tempora</p>
</div>

<section class="mission">
  <h2 class="mission-title heading">OUR MISSION</h2>
  <p class="mission-text">Nemo enim ipsam voluptatem quia voluptas sit aspernatur aut odit aut fugit, sed quia consequuntur magni dolores eos qui ratione voluptatem sequi nesciunt. Neque porro quisquam est, qui dolorem ipsum quia dolor sit amet, consectetur, adipisci velit, sed quia non numquam eius modi tempora incidunt ut labore et dolore magnam aliquam quaerat voluptatem.</p>
  <div class="mission-btn">Read More</div>
</section>

<h2 class="photos-title heading">OUR PHOTOS</h2>
<svg class="arrow" style="left:88px" width="26" height="50" viewBox="0 0 26 50"><polyline points="24,2 2,25 24,48" fill="none" stroke="#333" stroke-width="1.6"/></svg>
<div class="photo" style="left:131px;background:linear-gradient(135deg,#5a3a30,#8a5a48 50%,#3a2a24)" role="img" aria-label="Friends sharing a meal at a table"></div>
<div class="photo" style="left:369px;background:linear-gradient(135deg,#8a8078,#c8beb4 50%,#6a5a50)" role="img" aria-label="Volunteer preparing food in the church kitchen"></div>
<div class="photo" style="left:607px;background:linear-gradient(135deg,#6a4a3a,#9a6a55 50%,#4a3028)" role="img" aria-label="Members gathered in the hall for a social lunch"></div>
<div class="photo" style="left:843px;background:linear-gradient(135deg,#5a6a48,#9a9a88 50%,#4a4a40)" role="img" aria-label="Older members chatting outdoors"></div>
<svg class="arrow" style="left:1088px" width="26" height="50" viewBox="0 0 26 50"><polyline points="2,2 24,25 2,48" fill="none" stroke="#333" stroke-width="1.6"/></svg>

<section class="news">
  <h2 class="news-title heading">RECENT NEWS</h2>
  <article class="card" style="left:135px">
    <div class="card-image" style="background:linear-gradient(180deg,#8fb4d8 0%,#c9d6e0 45%,#5f6a5a 100%)" role="img" aria-label="Stone church with twin towers"></div>
    <div class="card-date"><span class="day">19</span><span class="mon">Oct</span></div>
    <h3 class="card-title heading">WE BELIEVE IN YOU</h3>
    <p class="card-text">Nemo enim ipsam voluptatem quia voluptas sit aspernatur aut odit aut fugit, sed quia consequuntur magni dolores eos</p>
  </article>
  <article class="card" style="left:457px">
    <div class="card-image" style="background:linear-gradient(180deg,#3a78c0 0%,#9ec2e2 45%,#c8a060 65%,#2a5a8a 100%)" role="img" aria-label="Harbour town with a domed church by the water"></div>
    <div class="card-date"><span class="day">19</span><span class="mon">Oct</span></div>
    <h3 class="card-title heading">WE BELIEVE IN YOU</h3>
    <p class="card-text">Nemo enim ipsam voluptatem quia voluptas sit aspernatur aut odit aut fugit, sed quia consequuntur magni dolores eos</p>
  </article>
  <article class="card" style="left:780px">
    <div class="card-image" style="background:linear-gradient(180deg,#5a6f8a 0%,#c8b89a 50%,#7a5a40 75%,#4a4a48 100%)" role="img" aria-label="Church on a town square under a cloudy sky"></div>
    <div class="card-date"><span class="day">19</span><span class="mon">Oct</span></div>
    <h3 class="card-title heading">WE BELIEVE IN YOU</h3>
    <p class="card-text">Nemo enim ipsam voluptatem quia voluptas sit aspernatur aut odit aut fugit, sed quia consequuntur magni dolores eos</p>
  </article>
</section>

<footer class="site-footer">
  <div class="footer-brand"><span class="brand-dot"></span><span class="brand-name">Briar Hollow Gathering Church</span></div>
  <div class="footer-col" style="left:495px">
    <div class="footer-head">QUICK LINKS</div>
    <ul class="quick-links">
      <li>Home</li><li>Age Group</li><li>Activites</li><li>Events</li><li>About BHGC</li><li>Contact</li>
    </ul>
  </div>
  <div class="footer-col" style="left:679px">
    <div class="footer-head">CONTACT US</div>
    <div class="contact-line"><svg width="10" height="13" viewBox="0 0 10 13"><path d="M5 0a5 5 0 0 0-5 5c0 3.5 5 8 5 8s5-4.5 5-8a5 5 0 0 0-5-5z" fill="#ddd"/><circle cx="5" cy="5" r="1.8" fill="#2b2b2b"/></svg><span>Lorem ipsum dolo<br>consectetur adipiscing elit</span></div>
    <div class="contact-line" style="margin-top:12px"><svg width="12" height="11" viewBox="0 0 12 11"><path d="M1 3c0-2 10-2 10 0v1H8V3H4v1H1z M2 5h8l1 6H1z" fill="#ddd"/></svg><span>555-014-2290</span></div>
    <div class="contact-line tight" style="margin-top:0"><svg width="12" height="9" viewBox="0 0 12 9"><rect width="12" height="9" fill="#ddd"/><polyline points="0,0 6,5 12,0" fill="none" stroke="#2b2b2b" stroke-width="1.2"/></svg><span>hello@briarhollow.example</span></div>
  </div>
  <div class="footer-col" style="left:901px">
    <div class="footer-head">FOLLOW US</div>
    <div class="socials"><span class="on"></span><span></span><span></span><span></span></div>
  </div>
</footer>
<div class="footer-base">Briar Hollow Gathering Church.® 2016 - All rights reserved.</div>

</body>
</html>
```